A new novel about the early days of The Quillmen needs a book cover design

The title of the book is LANTERN ROW NIGHTS
The cover should also include "a novel" and "by Milo Fastwick" Those can be together or separate.
The design element I'd like to incorporate is the iconic "Pier Lamps" photo of The Quillmen in 1960, which I've attached below. Since we're not sure if we can get the rights to the actual photo, it's probably best if the design merely references that photo, or distorts it in an interesting way. But it should be very clear that the book is about The Quillmen.
The novel is in many ways based on that photo and evokes the city of Hamburg in 1960, which was gritty, raw, and sexually charged (as were The Quillmen).
The tone of the novel is romantic, passionate, and very funny - but never broad and silly.

```html
<!DOCTYPE html>
<html lang="en">
<head>
<meta charset="utf-8">
<title>Lantern Row Nights – Book Cover</title>
<link href="https://fonts.googleapis.com/css2?family=Jost:wght@400&display=swap" rel="stylesheet">
<style>
  :root {
    --stage: #eb8a3f;
    --sky-top: #ffb35f;
    --sky-low: #ffe2cc;
    --ridge-dark: #cc0000;
    --hill-left: #e00000;
    --slope-main: #f70000;
    --slope-right: #e20000;
    --band-shadow: #c40000;
    --title-red: #f20000;
    --title-dark: #111111;
    --paper: #ffffff;
  }
  html, body {
    margin: 0;
    width: 1200px;
    height: 1200px;
    overflow: hidden;
    background: var(--stage);
  }
  .cover-spread {
    display: block;
    width: 1200px;
    height: 1200px;
  }
  .title-main {
    font-family: "Jost", sans-serif;
    font-weight: 400;
    font-size: 78px;
    fill: var(--title-red);
  }
  .title-sub {
    font-family: "Jost", sans-serif;
    font-weight: 400;
    font-size: 60px;
    fill: var(--title-dark);
  }
  .byline {
    font-family: "Jost", sans-serif;
    font-weight: 400;
    font-size: 35px;
    fill: var(--paper);
  }
  .byline-novel { letter-spacing: 24px; }
  .byline-by { letter-spacing: 6px; }
  .byline-author { letter-spacing: 28px; }
  .spine-frame {
    fill: none;
    stroke: var(--paper);
    stroke-width: 3;
  }
  .barcode-space { fill: var(--paper); }
</style>
</head>
<body>
<svg class="cover-spread" viewBox="0 0 1932 1932" xmlns="http://www.w3.org/2000/svg">
  <defs>
    <linearGradient id="sky" x1="0.35" y1="1" x2="0.55" y2="0.2">
      <stop offset="0" stop-color="var(--sky-low)"/>
      <stop offset="1" stop-color="var(--sky-top)"/>
    </linearGradient>
    <linearGradient id="band-fill" x1="0" y1="0" x2="0" y2="1">
      <stop offset="0" stop-color="var(--band-shadow)" stop-opacity="0.55"/>
      <stop offset="1" stop-color="var(--band-shadow)"/>
    </linearGradient>
  </defs>

  <rect class="sky" x="94" y="377" width="1738" height="1163" fill="url(#sky)"/>

  <polygon class="ridge" fill="var(--ridge-dark)"
    points="94,1075 347,1035 781,1076 1160,1013 1832,1013 1832,1540 94,1540"/>

  <rect class="band-silhouette" role="img"
    aria-label="Silhouette of the five-piece band with guitars, seated on the ridge"
    x="1158" y="876" width="592" height="138" fill="url(#band-fill)"/>

  <polygon class="hill-left" fill="var(--hill-left)" points="94,1190 860,1540 94,1540"/>
  <polygon class="slope-main" fill="var(--slope-main)" fill-opacity="0.92" points="924,1012 1832,1540 94,1540"/>
  <polygon class="slope-right" fill="var(--slope-right)" fill-opacity="0.85" points="1832,915 1832,1540 855,1540"/>

  <rect class="spine-frame" x="858" y="377" width="214" height="1163"/>

  <rect class="barcode-space" x="531" y="1352" width="240" height="109"/>

  <text class="title-main" x="1706" y="687" text-anchor="end">LANTERN ROW</text>
  <text class="title-sub" x="1708" y="762" text-anchor="end">NIGHTS</text>

  <text class="byline byline-novel" x="1466" y="1297" text-anchor="middle">A NOVEL</text>
  <text class="byline byline-by" x="1459" y="1350" text-anchor="middle">BY</text>
  <text class="byline byline-author" x="1474" y="1402" text-anchor="middle">MILO FASTWICK</text>
</svg>
</body>
</html>
```